Business Card Design for Occupational Medicine Start Up Company

We need to design a professional business card. We are a healthcare company providing occupational medicine services to blue collar industries. We are professional, efficient and high quality service providers.

Target Market(s)

Blue Collar Industry: Shipbuilding, Ports, Trucking Companies; The Executives and Safety Officers for these companies

Industry/Entity Type

Healthcare

Contact Information for Business Card

Logo, Name, Title, Email, Phone

Other font styles liked:
• Please match our Brand Guide

Requirements
Must have
• Our Company Colors and Logo

```html
<!DOCTYPE html>
<html lang="en">
<head>
<meta charset="utf-8">
<title>Crewline Health — Business Card</title>
<link href="https://fonts.googleapis.com/css2?family=Montserrat:wght@400;500;600;700&display=swap" rel="stylesheet">
<style>
  :root {
    --backdrop: #262626;
    --navy: #30307a;
    --navy-text: #2e2e76;
    --sky: #3598d4;
    --amber: #eea93a;
    --paper: #f4f4f2;
    --white: #ffffff;
  }
  html, body {
    margin: 0;
    padding: 0;
    width: 1200px;
    height: 1200px;
    overflow: hidden;
    background: var(--backdrop);
    font-family: "Montserrat", sans-serif;
  }
  .canvas {
    position: relative;
    width: 1200px;
    height: 1200px;
  }
  .card {
    position: absolute;
    width: 594px;
    height: 349px;
    border-radius: 22px;
    overflow: hidden;
  }
  .card-front {
    left: 298px;
    top: 198px;
    background: var(--navy);
  }
  .card-back {
    left: 292px;
    top: 637px;
    background: var(--paper);
  }

  /* Front */
  .front-brand {
    position: absolute;
    left: 0;
    right: 0;
    top: 88px;
    display: flex;
    flex-direction: column;
    align-items: center;
    gap: 22px;
  }
  .brand-dot {
    width: 62px;
    height: 62px;
    border-radius: 50%;
  }
  .front-brand .brand-dot { background: var(--sky); }
  .front-brand .brand-name {
    color: var(--white);
    font-weight: 600;
    font-size: 38px;
    letter-spacing: 1px;
    line-height: 1;
  }
  .front-url {
    position: absolute;
    left: 0;
    right: 0;
    top: 301px;
    text-align: center;
    color: var(--white);
    font-size: 16px;
    letter-spacing: 1.2px;
    line-height: 1;
  }
  .front-url .url-blue { color: var(--sky); }
  .front-url .url-amber { color: var(--amber); }

  /* Back */
  .back-brand {
    position: absolute;
    left: 80px;
    top: 57px;
    display: flex;
    align-items: center;
    gap: 22px;
  }
  .back-brand .brand-dot {
    width: 70px;
    height: 70px;
    background: var(--sky);
  }
  .back-brand .brand-name {
    color: var(--navy-text);
    font-weight: 600;
    font-size: 38px;
    letter-spacing: 1px;
    line-height: 1;
  }
  .person {
    position: absolute;
    left: 0;
    right: 0;
    top: 182px;
    text-align: center;
  }
  .person-name {
    color: var(--sky);
    font-weight: 600;
    font-size: 25px;
    letter-spacing: 0.5px;
    line-height: 1;
  }
  .person-title {
    margin-top: 6px;
    color: var(--navy-text);
    font-size: 15.5px;
    line-height: 1;
  }
  .contact-row {
    position: absolute;
    left: 0;
    right: 0;
    display: flex;
    justify-content: center;
    align-items: center;
    gap: 16px;
    color: var(--navy-text);
    font-size: 15.5px;
    line-height: 1;
    white-space: nowrap;
  }
  .contact-row.primary { top: 256px; }
  .contact-row.address { top: 280px; }
  .contact-item {
    display: flex;
    align-items: center;
    gap: 9px;
  }
  .contact-icon {
    width: 14px;
    height: 14px;
    flex: none;
  }
</style>
</head>
<body>
<main class="canvas">

  <section class="card card-front" aria-label="Card front">
    <div class="front-brand">
      <span class="brand-dot"></span>
      <span class="brand-name">CREWLINE HEALTH</span>
    </div>
    <p class="front-url" style="margin:0">www.<span class="url-blue">crewline</span><span class="url-amber">healthcare</span>.com</p>
  </section>

  <section class="card card-back" aria-label="Card back">
    <div class="back-brand">
      <span class="brand-dot"></span>
      <span class="brand-name">CREWLINE HEALTH</span>
    </div>

    <div class="person">
      <div class="person-name">DANA REYES</div>
      <div class="person-title">Senior Doctor</div>
    </div>

    <div class="contact-row primary">
      <span class="contact-item">
        <svg class="contact-icon" viewBox="0 0 16 16" aria-hidden="true">
          <path fill="#3598d4" d="M1 5c0-2 3-3 7-3s7 1 7 3v1h-3.5V4.5h-7V6H1z"/>
          <path fill="#3598d4" d="M3 7h10l1.5 7h-13z"/>
          <circle cx="8" cy="10.5" r="1.8" fill="#f4f4f2"/>
        </svg>
        555-201-4870
      </span>
      <span class="contact-item">
        <svg class="contact-icon" viewBox="0 0 16 16" aria-hidden="true">
          <rect x="1" y="3.5" width="14" height="9.5" fill="#2e2e76"/>
          <path d="M1.5 4l6.5 5 6.5-5" fill="none" stroke="#f4f4f2" stroke-width="1.4"/>
        </svg>
        hello@crewlinehealth.com
      </span>
      <span class="contact-item">
        <svg class="contact-icon" viewBox="0 0 16 16" aria-hidden="true">
          <circle cx="8" cy="8" r="6.5" fill="#eea93a"/>
          <g fill="none" stroke="#f4f4f2" stroke-width="0.9">
            <ellipse cx="8" cy="8" rx="2.8" ry="6.5"/>
            <path d="M1.5 8h13M2.5 5h11M2.5 11h11"/>
          </g>
        </svg>
        crewlinehealth.com
      </span>
    </div>

    <div class="contact-row address">
      <span class="contact-item">
        <svg class="contact-icon" viewBox="0 0 16 16" aria-hidden="true">
          <path fill="#eea93a" d="M8 1a5 5 0 0 0-5 5c0 3.6 5 9 5 9s5-5.4 5-9a5 5 0 0 0-5-5z"/>
          <circle cx="8" cy="6" r="2" fill="#f4f4f2"/>
        </svg>
        48 Harbor Avenue, Suite 210, Port City, State 54321
      </span>
    </div>
  </section>

</main>
</body>
</html>
```